Covid 19 Exit Strategy one page brochure

I would like to design, and will need URGENT help, a brochure detailing a Covid 19 Exit Strategy plan. This brochure will need to be understood easily and the graphics inside should make it easy for people to understand without reading the entire text. This project is quite urgent and needs to be completed THIS WEEK - by Saturday may 16th at the latest. I am attaching two examples. I will provide the text.

```html
<!DOCTYPE html>
<html lang="en">
<head>
<meta charset="utf-8">
<title>Covid-19 Phased Social &amp; Economical Restart</title>
<link href="https://fonts.googleapis.com/css2?family=Montserrat:wght@400;500;700;800&display=swap" rel="stylesheet">
<style>
:root{
  --backdrop:#7e7b88;
  --paper:#ffffff;
  --teal:#00b3d1;
  --red:#c91c33;
  --ink:#1c1c1c;
  --ring:#d8232f;
}
*{box-sizing:border-box;margin:0;padding:0}
html,body{width:1200px;height:2970px;overflow:hidden;background:var(--backdrop);font-family:"Montserrat",sans-serif;color:var(--ink)}
.sheet{position:absolute;left:52px;width:1090px;height:1409px;background:var(--paper);box-shadow:0 4px 10px rgba(0,0,0,.35);overflow:hidden}
.sheet-one{top:43px}
.sheet-two{top:1522px}
.abs{position:absolute}
.band{position:absolute;left:0;width:100%}
.band-teal{background:var(--teal)}
.band-red{background:var(--red)}
.title{left:31px;top:54px;font-size:62px;font-weight:400;letter-spacing:.5px;line-height:1}
.subtitle{left:31px;top:113px;font-size:28px;font-weight:400;line-height:1.1}
.tagline{left:31px;top:153px;font-size:28px;font-weight:400;color:var(--teal);line-height:1.1}
.author{left:31px;top:197px;width:542px;height:53px;background:var(--teal);color:#fff;font-weight:700;font-size:28px;display:flex;align-items:center;justify-content:center;letter-spacing:.5px}
.intro{left:31px;top:259px;width:547px;font-size:11.2px;line-height:15px;text-align:justify;letter-spacing:-.15px}
.accent-rule{left:29px;top:426px;width:63px;height:4px;background:var(--red)}
.section-title{left:29px;top:438px;font-size:19px;font-weight:800}
.photo{left:600px;top:90px;width:462px;height:492px}
.item{position:absolute;display:flex;gap:9px;align-items:flex-start;font-size:11.2px;line-height:15px;letter-spacing:-.15px}
.item p{flex:1;text-align:justify}
.icon{flex:none;width:42px;height:42px;border-radius:50%;background:#fff;border:2px solid var(--ring);display:flex;align-items:center;justify-content:center}
.icon::after{content:"";width:22px;height:22px;border-radius:6px;background:linear-gradient(135deg,#f2b33d,#e05a3a 55%,#3a8fc7)}
.on-teal,.on-red{color:#fff}
.plan-heading{top:860px;left:0;width:100%;text-align:center;color:#fff;font-weight:700;font-size:20px;letter-spacing:11.5px}
.stage{position:absolute;display:flex;align-items:center;height:61px}
.stage-light{background:#fff}
.stage-red{background:var(--red);color:#fff}
.stage-name{font-weight:800;font-size:29px;letter-spacing:.5px;white-space:nowrap}
.stage-divider{width:2px;align-self:stretch;margin:6px 9px 6px 0}
.stage-text{font-size:11.2px;line-height:14.5px;letter-spacing:-.15px}
.stage-text b{font-weight:700}
.notch{position:absolute;left:0;top:50%;transform:translateY(-50%);width:0;height:0;border-top:10px solid transparent;border-bottom:10px solid transparent}
</style>
</head>
<body>

<section class="sheet sheet-one">
  <h1 class="abs title">COVID-19</h1>
  <p class="abs subtitle">Phased Social &amp; Economical Restart</p>
  <p class="abs tagline">A Global Benchmark of Best Practices</p>
  <div class="abs author">LENA OKAFOR</div>
  <p class="abs intro">Pandemics have, historically, seen their end both medically - via herd immunity or immunizations. And while there are several clinical trials underway for potential Covid-19 vaccines, we are still a long way from deploying an effective vaccine and one that will stand the test of time as the virus changes. Covid-19 pandemic will be considered 'ended' when there are only occasional traces of localized cases that are quickly contained in specific locations., Today and in the absence of an effective vaccine(s) and for the re-opening of the economies and social activities to be successful, it is critical that the following basic conditions be in place before any lockdowns are lifted and before social activities resume:</p>

  <svg class="abs photo" viewBox="0 0 462 492" role="img" aria-label="Photo of four young people in surgical masks crossing their arms in a stop gesture">
    <defs><linearGradient id="photoTone" x1="0" y1="0" x2="1" y2="1"><stop offset="0" stop-color="#9fb2bd"/><stop offset=".5" stop-color="#8a7a6c"/><stop offset="1" stop-color="#c9c3bd"/></linearGradient></defs>
    <path fill="url(#photoTone)" d="M10 150 C0 90 60 80 95 110 C120 60 130 10 190 5 C250 0 250 60 260 80 C300 40 400 60 440 150 C470 220 450 320 420 380 C380 460 300 495 220 490 C130 485 60 430 45 350 C35 290 20 220 10 150 Z"/>
  </svg>

  <div class="abs accent-rule"></div>
  <h2 class="abs section-title">GENERAL REQUIREMENTS</h2>

  <div class="item" style="left:30px;top:490px;width:258px"><span class="icon" role="img" aria-label="Shield icon"></span><p>Single digit downward trend of documented cases within the past 14- days.</p></div>
  <div class="item" style="left:327px;top:490px;width:256px"><span class="icon" role="img" aria-label="Hospital icon"></span><p>Hospitals and the health care system are capable of treating patients without operating on a crisis mode.</p></div>
  <div class="item" style="left:30px;top:575px;width:258px"><span class="icon" role="img" aria-label="Test tube icon"></span><p>Ability to screen and test symptomatic individuals within 24 hours of identification. Increased and sufficient testing capacity, to test at least 50% of all population if necessary within a timeframe of 3 months.</p></div>
  <div class="item" style="left:327px;top:568px;width:256px"><span class="icon" role="img" aria-label="Monitor icon"></span><p>Ability to surge ICU capacity on a short notice - 24h.</p></div>
  <div class="item" style="left:327px;top:639px;width:414px"><span class="icon" role="img" aria-label="Virus alert icon"></span><p>Plan in place to trigger targeted or full-scale containment in case of sudden outbreaks</p></div>
  <div class="item" style="left:806px;top:621px;width:256px"><span class="icon" role="img" aria-label="Thermometer icon"></span><p>Mandatory daily checks of body temperature for everyone at the workplace or entering public areas.</p></div>
  <div class="item" style="left:35px;top:715px;width:263px"><span class="icon" role="img" aria-label="Tracking icon"></span><p>Ability to track and trace infected patients and contacts on a live basis and across the country and ability to react quickly to any unusual trends or outbreaks.</p></div>
  <div class="item" style="left:327px;top:715px;width:447px"><span class="icon" role="img" aria-label="Mask icon"></span><p>Mandatory use of masks (at least surgical grade) for everyone in all public areas and at work. Mandatory use of N95, or equivalent, masks for all healthcare front workers and for all government agencies and authorities that are involved in overseeing the containment activities.</p></div>
  <div class="item" style="left:806px;top:715px;width:256px"><span class="icon" role="img" aria-label="Sanitizer icon"></span><p>Mandatory sanitation in all places - use of disinfection available on a large scale.</p></div>

  <div class="band band-teal" style="top:846px;height:563px"></div>
  <h2 class="abs plan-heading">PHASED COVID-19 LOCKDOWN EXIT STRATEGY PLAN</h2>

  <div class="stage stage-light" style="left:163px;top:910px;width:745px">
    <span class="notch" style="border-left:12px solid var(--teal)"></span>
    <span class="stage-name" style="color:var(--teal);margin:0 22px 0 40px">STAGE 1</span>
    <span class="stage-divider" style="background:var(--teal)"></span>
    <p class="stage-text">To enter this stage, additional to the general requirements, the Effective<br>Reproduction Number (Rt) must be less than 1 and the death rate at less than 3%.<br><b>The economy and social activities can resume in this sequence:</b></p>
  </div>

  <div class="item on-teal" style="left:30px;top:1017px;width:258px"><span class="icon" role="img" aria-label="Elderly people icon"></span><p>Elderly (60+ years old) and vulnerable individuals should continue to self-isolate.</p></div>
  <div class="item on-teal" style="left:30px;top:1081px;width:258px"><span class="icon" role="img" aria-label="Group limit icon"></span><p>No more than 5 people maximum gathering at a time in public areas and at work.</p></div>
  <div class="item on-teal" style="left:30px;top:1153px;width:258px"><span class="icon" role="img" aria-label="Home icon"></span><p>Work from home should continue whenever and as much as possible.</p></div>
  <div class="item on-teal" style="left:30px;top:1227px;width:258px"><span class="icon" role="img" aria-label="Distancing icon"></span><p>Social distancing should continue to be re-enforced in public areas, at work and in all areas reopened.</p></div>
  <div class="item on-teal" style="left:30px;top:1310px;width:258px"><span class="icon" role="img" aria-label="Map pin icon"></span><p>Non-essential travel should be minimized between cities and regions (and within cities and regions where covid-19 infections are still a risk)</p></div>

  <div class="item on-teal" style="left:325px;top:1017px;width:364px"><span class="icon" role="img" aria-label="Office building icon"></span><p>Large businesses (300 people and more, manufacturing, services, etc.) can reopen progressively. Common areas should remain closed (cafeteria, restaurant, gym, meeting rooms of no more than 5 people).</p></div>
  <div class="item on-teal" style="left:325px;top:1116px;width:364px"><span class="icon" role="img" aria-label="Briefcase icon"></span><p>Small businesses (300 people and less) can reopen as well with the same conditions as large businesses.</p></div>
  <div class="item on-teal" style="left:325px;top:1187px;width:364px"><span class="icon" role="img" aria-label="Shop icon"></span><p>Commercial shops can reopen. Shops should control the flow of people in their facilities not to exceed 30% at a time of standard capacity. Shops should provide disinfectant and temperature control at entry.</p></div>
  <div class="item on-teal" style="left:325px;top:1284px;width:364px"><span class="icon" role="img" aria-label="Pharmacy icon"></span><p>Pharmacies will continue to be open. However, they must make available disinfectant for use by clients and will continue to comply with social distancing. Pharmacies should limit the number of client/patient in their stores not to exceed 30% of the standard capacity.</p></div>

  <div class="item on-teal" style="left:710px;top:1017px;width:352px"><span class="icon" role="img" aria-label="Transport icon"></span><p>Transportation (buses, taxis, airlines) will resume progressively. No air travels permitted in and out of Covid-19 known hotspots, locally or internationally. Entry to country should be limited and strictly controlled. All landing passengers and visitors regardless of the country of origin should be tested for Covid-19 at arrival. All passengers and visitors will undergo a temperature check at arrival. No more than 3 people at a time in a taxi/Rydo including the driver. All passengers wearing masks. Buses should operate with no more than 30% customer's capacity per bus.</p></div>
  <div class="item on-teal" style="left:721px;top:1275px;width:353px"><span class="icon" role="img" aria-label="Praying hands icon"></span><p>Religious sites can reopen with a maximum capacity of 30% or less. Social distancing and wearing masks is mandatory. Religious sites should organize (volunteers can help) to check body temperature of everyone accessing the site and provide disinfectant at entry.</p></div>
</section>

<section class="sheet sheet-two">
  <div class="band band-teal" style="top:0;height:213px"></div>
  <div class="item on-teal" style="left:28px;top:38px;width:475px"><span class="icon" role="img" aria-label="Hotel icon"></span><p>Hotels &amp; tourism (museums, etc.) can reopen but must operate at 30% or less capacity. All common areas (restaurants, gyms, swimming pools, conference rooms, etc.) should remain closed.</p></div>
  <div class="item on-teal" style="left:28px;top:121px;width:475px"><span class="icon" role="img" aria-label="Cafe icon"></span><p>Coffee &amp; restaurants can reopen but must operate at 30% capacity as well and comply with social distancing. Clients must wear as much as possible their masks if they are not consuming food/coffee. Clients should avoid to talking to each other with masks off.</p></div>
  <div class="item on-teal" style="left:572px;top:38px;width:466px"><span class="icon" role="img" aria-label="School icon"></span><p>All schools should remain closed. On-line courses should continue be the preferred method for education</p></div>
  <div class="item on-teal" style="left:572px;top:121px;width:466px"><span class="icon" role="img" aria-label="Events icon"></span><p>Large scale events (cinema, theaters, sport, business conferences, etc.) should remain closed or operate virtually. Sport events can resume but without spectators. Athletes and the staff surrounding them should be tested, disinfectants should be available and masks used as much as reasonably possible.</p></div>

  <div class="stage stage-red" style="left:151px;top:239px;width:746px">
    <span class="notch" style="border-left:12px solid #fff"></span>
    <span class="stage-name" style="margin:0 16px 0 39px">STAGE 2</span>
    <span class="stage-divider" style="background:#fff"></span>
    <p class="stage-text">To enter this stage, additional to the general requirements, the Effective<br>Reproduction Number (Rt) must be less than 1 and the death rate at less than 3%.<br><b>The economy and social activities can resume in this sequence:</b></p>
  </div>

  <div class="item" style="left:30px;top:330px;width:258px"><span class="icon" role="img" aria-label="Elderly people icon"></span><p>Elderly (60+ years old) and vulnerable individuals should continue to self-isolate as much as possible. If</p></div>
  <div class="item" style="left:30px;top:473px;width:258px"><span class="icon" role="img" aria-label="Group limit icon"></span><p>No more than 10 people maximum gathering at a time in public areas and at work.</p></div>
  <div class="item" style="left:30px;top:583px;width:258px"><span class="icon" role="img" aria-label="Home icon"></span><p>Work from home should if possible or for jobs that do not have to be necessarily in an office setup.</p></div>
  <div class="item" style="left:30px;top:700px;width:258px"><span class="icon" role="img" aria-label="Mask icon"></span><p>Social distancing can be relaxed. However people should continue to wear masks and use disinfectants</p></div>
  <div class="item" style="left:30px;top:814px;width:258px"><span class="icon" role="img" aria-label="Map pin icon"></span><p>Travel can resume between cities and regions. The same containment restrictions should apply to any existing hotspot.</p></div>

  <div class="item" style="left:313px;top:330px;width:257px"><span class="icon" role="img" aria-label="Surgery icon"></span><p>Elective surgeries can resume in hospitals and clinics that are equipped to comply with all general requirements.</p></div>
  <div class="item" style="left:313px;top:443px;width:257px"><span class="icon" role="img" aria-label="Office building icon"></span><p>Large businesses (300 people and more, manufacturing, services, etc.) will continue to operate. Common areas should open but social distancing should remain (cafeteria, restaurant, gym, meeting rooms of no more than 10 people).</p></div>
  <div class="item" style="left:313px;top:602px;width:257px"><span class="icon" role="img" aria-label="Briefcase icon"></span><p>Small businesses (300 people and less) will continue to operate with the same conditions as large businesses.</p></div>
  <div class="item" style="left:313px;top:700px;width:257px"><span class="icon" role="img" aria-label="Shop icon"></span><p>Commercial shops will continue to be open and can operate at 50% capacity. Wear of masks should continue.</p></div>
  <div class="item" style="left:313px;top:808px;width:257px"><span class="icon" role="img" aria-label="Pharmacy icon"></span><p>Pharmacies will continue to be open and will need to operate a 50% capacity</p></div>

  <div class="item" style="left:621px;top:330px;width:437px"><span class="icon" role="img" aria-label="Transport icon"></span><p>Transportation (buses, taxis, and airlines) will continue to operate. Still no air travels permitted in and out of Covid-19 known hotspots, locally or internationally. Entry to country should be relaxed but remain controlled. Airports should continue to use thermo cameras to monitor passenger's temperature at landing. Airports should be equipped to test for Covid-19 if necessary. Transportation by taxi/Rydo continues, however, passengers wear masks. Buses could operate with 50% capacity per bus.</p></div>
  <div class="item" style="left:621px;top:488px;width:437px"><span class="icon" role="img" aria-label="Praying hands icon"></span><p>Religious sites can operate with a maximum capacity of 50%. Social distancing and wearing masks should be enforced. Sites should continue to check body temperature of everyone accessing the site and provide disinfectant at entry.</p></div>
  <div class="item" style="left:621px;top:571px;width:437px"><span class="icon" role="img" aria-label="Hotel icon"></span><p>Hotels &amp; tourism (museums, etc.) can operate at 50% capacity. All common areas (restaurants, gyms, swimming pools, conference rooms, etc.) could reopen. Gatherings are limited to 10 people or less and can be expanded with social distancing and wearing protective masks.</p></div>
  <div class="item" style="left:621px;top:663px;width:437px"><span class="icon" role="img" aria-label="Cafe icon"></span><p>Coffee &amp; restaurants can operate at 50% capacity and continue comply with social distancing. Clients must wear as much as possible their masks if they are not consuming food/coffee.</p></div>
  <div class="item" style="left:621px;top:745px;width:437px"><span class="icon" role="img" aria-label="School icon"></span><p>Schools can reopen in parallel with on-line education. Social distancing and re-arranging school seating to prevent the spread of infection is mandatory</p></div>
  <div class="item" style="left:621px;top:808px;width:437px"><span class="icon" role="img" aria-label="Events icon"></span><p>Large scale events (cinema, theaters, sport, business conferences, etc.) could resume under strict social distancing. People should wear masks.</p></div>

  <div class="band band-red" style="top:897px;height:512px"></div>
  <div class="stage stage-light" style="left:96px;top:903px;width:901px;height:75px">
    <span class="notch" style="border-left:12px solid var(--red)"></span>
    <span class="stage-name" style="color:var(--red);margin:0 16px 0 37px">STAGE 3</span>
    <span class="stage-divider" style="background:var(--red)"></span>
    <p class="stage-text">To enter stage 3 of the Covid-19 Exit Strategy, compliance to the general requirements is compulsory, additional to a successful Stage 2 outcome. The Effective Reproduction Number (Rt) for Stage 3 must be less than 0.3 and the death rate stabilized at less than 1%.<br><b>The economy and social activities can resume in this sequence:</b></p>
  </div>

  <div class="item on-red" style="left:30px;top:1008px;width:329px"><span class="icon" role="img" aria-label="Elderly person icon"></span><p>Elderly (60+ years old) and vulnerable individuals may resume all previously exercised activities without restrictions. Restrictions as to the number of people gathering together can be lifted. Social distancing can be relaxed. However, wear of masks may continue.</p></div>
  <div class="item on-red" style="left:30px;top:1135px;width:352px"><span class="icon" role="img" aria-label="Luggage icon"></span><p>Travel can resume between cities and regions and out of country travel. The same containment restrictions as Stage 1 and 2 would continue to apply to any existing hotspot</p></div>
  <div class="item on-red" style="left:30px;top:1235px;width:352px"><span class="icon" role="img" aria-label="Hospital bed icon"></span><p>All hospital and clinic surgeries can resume in hospitals in compliance with standard hospital and health care procedures.</p></div>
  <div class="item on-red" style="left:30px;top:1326px;width:352px"><span class="icon" role="img" aria-label="Office building icon"></span><p>Large businesses (300 people and more, manufacturing, services, etc.) will resume normal business practices. Wear of masks is recommended but not mandatory.</p></div>

  <div class="item on-red" style="left:394px;top:1008px;width:353px"><span class="icon" role="img" aria-label="Briefcase icon"></span><p>Small businesses (300 people and less) will operate with the same conditions as large businesses.</p></div>
  <div class="item on-red" style="left:394px;top:1080px;width:353px"><span class="icon" role="img" aria-label="Shop icon"></span><p>Commercial shops can operate on a normal mode - previous to covid- 19. Wear of masks could be recommended in certain areas</p></div>
  <div class="item on-red" style="left:394px;top:1167px;width:353px"><span class="icon" role="img" aria-label="Pharmacy icon"></span><p>Pharmacies can operate at a normal state.</p></div>
  <div class="item on-red" style="left:394px;top:1219px;width:353px"><span class="icon" role="img" aria-label="Transport icon"></span><p>Transportation (buses, taxis, and airlines) will operate at a normal capacity. Still no air travels permitted in and out of Covid-19 known hotspots, locally or internationally. Entry to country should be relaxed and operate normally. Airports should continue to use thermo cameras to monitor passenger's temperature at landing. Airports should be equipped to test for Covid-19 if necessary. Transportation by taxi/Rydo and buses will resume on a normal mode. Wear of masks is elective.</p></div>

  <div class="item on-red" style="left:768px;top:1008px;width:291px"><span class="icon" role="img" aria-label="Praying hands icon"></span><p>Religious sites can operate normally. Wear of masks should be elective</p></div>
  <div class="item on-red" style="left:768px;top:1072px;width:291px"><span class="icon" role="img" aria-label="Hotel icon"></span><p>Hotels &amp; tourism (museums, etc.) can operate at 100% capacity including all common areas</p></div>
  <div class="item on-red" style="left:768px;top:1153px;width:291px"><span class="icon" role="img" aria-label="Cafe icon"></span><p>Coffee &amp; restaurants can resume normal operations. Clients may wear masks for personal protection if they wish to.</p></div>
  <div class="item on-red" style="left:768px;top:1240px;width:291px"><span class="icon" role="img" aria-label="School icon"></span><p>Schools can resume operations. Re-arranging school seating should continue until a vaccine is found.</p></div>
  <div class="item on-red" style="left:768px;top:1314px;width:291px"><span class="icon" role="img" aria-label="Mask icon"></span><p>Large scale events (cinema, theaters, sport, business conferences, etc) could resume under moderate social distancing. People may elect to wear masks.</p></div>
</section>

</body>
</html>
```